Silver Bloom Marisol's Cleaning Service Business Cards Project

A business card with all contact details with logo design on there (already have a logo) eye catching Logo and contact info on one side, full logo on the back, must target upper class residential and corporate companies, fitness companies, still keep it on the feminine side of things , must look elegant

Target Market(s)

Upper class homes and corporate companies

Industry/Entity Type

Cleaning Service

Contact Information for Business Card

Name: Marisol Quenby
Position: Director
ABN: 31647209853
Email: marisolssilvercleaning@tidymail.example
Number: 0417906354

Font styles to use
Decorative

Colors

Designer to choose colors to be used in the design.

Requirements
Must have
• Available Sydney Wide, contact info and logo on one side, full logo on the back
Nice to have
• Professional appearance
Should not have
• Cheap advert looking stuff

```html
<!DOCTYPE html>
<html lang="en">
<head>
<meta charset="utf-8">
<title>Silver Bloom – Business Cards</title>
<link rel="stylesheet" href="https://fonts.googleapis.com/css2?family=Rokkitt:wght@400;700;800&family=Roboto:wght@400&display=swap">
<style>
  :root {
    --backdrop: #b8b8b8;
    --card-dark: #2f3340;
    --aqua: #33e5dc;
    --aqua-text: #35d6c9;
    --aqua-soft: rgba(53, 214, 201, 0.22);
    --white: #ffffff;
    --white-soft: rgba(255, 255, 255, 0.32);
  }
  * { margin: 0; padding: 0; box-sizing: border-box; }
  html, body {
    width: 1200px;
    height: 960px;
    overflow: hidden;
  }
  body {
    position: relative;
    background: var(--backdrop);
    font-family: "Rokkitt", Georgia, serif;
  }
  .card {
    position: absolute;
    width: 600px;
    height: 343px;
  }
  .card--front {
    left: 322px;
    top: 108px;
    background: var(--card-dark);
    color: var(--white);
  }
  .card--back {
    left: 320px;
    top: 493px;
    background: var(--aqua);
    color: var(--white);
  }

  /* brand lock-up */
  .brand-mark {
    position: absolute;
    border-radius: 50%;
  }
  .card--front .brand-mark {
    left: 97px; top: 34px;
    width: 58px; height: 58px;
    border: 2px solid var(--aqua-text);
  }
  .card--back .brand-mark {
    left: 262px; top: 72px;
    width: 76px; height: 76px;
    border: 2px solid var(--white);
  }
  .flourish {
    position: absolute;
    border-radius: 20px;
  }
  .card--front .flourish {
    left: 30px; top: 100px;
    width: 191px; height: 36px;
    background: var(--aqua-soft);
  }
  .card--back .flourish {
    left: 147px; top: 160px;
    width: 306px; height: 56px;
    background: var(--white-soft);
  }
  .brand-name {
    position: absolute;
    text-align: center;
    font-family: "Rokkitt", Georgia, serif;
    font-weight: 400;
    text-transform: uppercase;
    line-height: 1;
  }
  .brand-name .title { display: block; letter-spacing: 1px; }
  .brand-name .tagline { display: block; letter-spacing: 2px; }
  .card--front .brand-name {
    left: 20px; top: 146px;
    width: 211px;
    color: var(--aqua-text);
  }
  .card--front .brand-name .title { font-size: 21px; }
  .card--front .brand-name .tagline { font-size: 9px; margin-top: 8px; }
  .card--back .brand-name {
    left: 0; top: 226px;
    width: 600px;
    color: var(--white);
  }
  .card--back .brand-name .title { font-size: 24px; }
  .card--back .brand-name .tagline { font-size: 10px; margin-top: 6px; }

  /* contact block */
  .contact {
    position: absolute;
    left: 31px;
    top: 227px;
    font-size: 16px;
    line-height: 19.5px;
  }
  .contact .abn { margin-bottom: 9px; }
  .contact .web { letter-spacing: 1px; }

  .sparkles {
    position: absolute;
    left: 346px;
    top: 224px;
  }
  .name-tag {
    position: absolute;
    left: 382px;
    top: 243px;
    width: 218px;
    height: 52px;
    background: var(--aqua);
    text-align: right;
    padding: 7px 17px 0 0;
    font-weight: 800;
    text-transform: uppercase;
    line-height: 1;
  }
  .name-tag .person { font-size: 21px; letter-spacing: 0.3px; }
  .name-tag .role { font-size: 15px; margin-top: 3px; letter-spacing: 0.5px; }

  .back-web {
    position: absolute;
    left: 0;
    top: 289px;
    width: 600px;
    text-align: center;
    font-family: "Roboto", Arial, sans-serif;
    font-size: 14px;
    letter-spacing: 4px;
  }
</style>
</head>
<body>
  <section class="card card--front">
    <span class="brand-mark"></span>
    <div class="flourish" role="img" aria-label="Decorative floral flourish in aqua line work"></div>
    <div class="brand-name">
      <span class="title">Silver Bloom</span>
      <span class="tagline">Marisol's Cleaning Service</span>
    </div>
    <div class="contact">
      <p class="abn">ABN: 31647209853</p>
      <p>(P) 0417906354</p>
      <p>marisolssilvercleaning@tidymail.example</p>
      <p class="web">www.silverbloom.example</p>
    </div>
    <svg class="sparkles" width="36" height="36" viewBox="0 0 36 36" aria-hidden="true">
      <path d="M12 2 L12 22 M2 12 L22 12" stroke="#33e5dc" stroke-width="2"/>
      <path d="M27 24 L27 34 M22 29 L32 29" stroke="#33e5dc" stroke-width="1.5"/>
    </svg>
    <div class="name-tag">
      <p class="person">Marisol Quenby</p>
      <p class="role">Director</p>
    </div>
  </section>

  <section class="card card--back">
    <span class="brand-mark"></span>
    <div class="flourish" role="img" aria-label="Decorative floral flourish in white line work"></div>
    <div class="brand-name">
      <span class="title">Silver Bloom</span>
      <span class="tagline">Marisol's Cleaning Service</span>
    </div>
    <p class="back-web">www.silverbloom.example</p>
  </section>
</body>
</html>
```